Webdesign für Projektmanagement
Zielgruppe
Projektmanagement und Projektsteuerung von Bauvorhaben für Projektentwickler und Bauträger.
Wesentliche Bereiche sind Wirtschaftliche Steuerung, Steuerung der Baustelle und Bauabläufe sowie Steuerung der Marketing und Vertriebsaktivitäten.
Aufgabenstellung
Orientierung am Logo. Logo und Visitenkarte liegen bei. Schriftart Prelo und Prelo Slab.

```html
<!DOCTYPE html>
<html lang="de">
<head>
<meta charset="utf-8">
<title>Brandtner Real Estate – Projektmanagement</title>
<link rel="stylesheet" href="https://fonts.googleapis.com/css2?family=Raleway:ital,wght@0,300;0,400;0,600;0,700;1,400&display=swap">
<style>
  :root{
    --navy:#03253f;
    --navy-deep:#021c31;
    --gold:#a48b45;
    --white:#ffffff;
    --card:#f1f1f1;
    --text:#3a3a3a;
    --muted:#777777;
    --rule:#ececec;
    --steel-a:#1f2f41;
    --steel-b:#3e4d5f;
    --steel-c:#59687a;
  }
  *{box-sizing:border-box;margin:0;padding:0}
  html,body{width:1036px;height:1200px;overflow:hidden}
  body{background:var(--navy);font-family:"Raleway",sans-serif;position:relative}
  .site{position:absolute;left:18px;top:312px;width:1000px;height:576px;display:flex;box-shadow:0 10px 30px rgba(0,0,0,.35)}
  .sidebar{width:152px;height:100%;background:var(--white);position:relative}
  .logo{position:absolute;left:22px;top:54px;color:var(--navy);font-weight:700;line-height:1}
  .logo .name{display:block;font-size:22px;letter-spacing:-.2px}
  .logo .sub{display:block;font-size:11px;margin-top:3px;text-align:right}
  .nav{position:absolute;top:141px;left:0;right:0;list-style:none;border-top:1px solid var(--rule)}
  .nav li{height:30.6px;border-bottom:1px solid var(--rule);display:flex;align-items:center;justify-content:space-between;padding:0 16px 0 23px;font-size:9px;color:var(--navy);letter-spacing:.3px;text-transform:uppercase}
  .nav li.active{color:var(--gold);font-weight:700}
  .nav .chev{color:var(--muted);font-size:9px}
  .nav li.search{text-transform:none;color:#999;font-style:italic;justify-content:flex-start;gap:7px}
  .social{position:absolute;bottom:18px;left:0;right:0;display:flex;justify-content:center;gap:11px}
  .social span{width:8px;height:8px;border-radius:50%;background:var(--navy);display:block}
  .main{flex:1;position:relative;overflow:hidden}
  .photo{position:absolute;inset:0;background:linear-gradient(125deg,var(--steel-a) 0%,var(--steel-b) 55%,var(--steel-c) 80%,var(--steel-b) 100%)}
  .photo::after{content:"";position:absolute;inset:0;background:rgba(10,25,42,.35)}
  .topbar{position:absolute;top:0;left:0;right:0;height:30px;background:rgba(255,255,255,.05);display:flex;align-items:center;gap:17px;padding-left:53px;color:var(--white);font-size:8.5px}
  .topbar .item{display:flex;align-items:center;gap:5px}
  .topbar svg{width:9px;height:9px;fill:var(--gold)}
  .kicker{position:absolute;left:53px;top:152px;color:var(--gold);font-weight:700;font-size:15px;letter-spacing:.3px}
  .headline{position:absolute;left:51px;top:190px;color:var(--white);font-weight:300;font-size:47px;line-height:57px;letter-spacing:.5px}
  .cards{position:absolute;left:53px;top:342px;display:flex;gap:9px}
  .card{width:200px;height:141px;background:var(--card);position:relative;padding:10px 12px 0}
  .card .cat{font-style:italic;font-size:8.5px;color:var(--muted)}
  .card h3{color:var(--gold);font-size:9.5px;font-weight:600;line-height:13px;margin-top:7px;text-transform:uppercase}
  .card p{font-size:8.5px;line-height:13px;color:var(--text);margin-top:6px}
  .card .more{position:absolute;right:0;bottom:0;width:76px;height:20px;background:var(--navy);color:var(--white);font-size:7.5px;font-weight:700;display:flex;align-items:center;justify-content:center;letter-spacing:.2px}
  .footer{position:absolute;left:0;right:0;bottom:0;height:35px;background:rgba(255,255,255,.05);color:var(--white);font-size:9px;display:flex;align-items:center;padding-left:53px}
</style>
</head>
<body>
  <div class="site">
    <aside class="sidebar">
      <div class="logo"><span class="name">Brandtner</span><span class="sub">Real Estate</span></div>
      <ul class="nav">
        <li class="active">Home</li>
        <li>Leistungen</li>
        <li>Über uns <span class="chev">›</span></li>
        <li>Projekte <span class="chev">›</span></li>
        <li>Partner</li>
        <li>Kontakt</li>
        <li class="search"><svg width="7" height="7" viewBox="0 0 10 10"><circle cx="4" cy="4" r="3" fill="none" stroke="#a48b45" stroke-width="1.6"/><path d="M6.2 6.2 9.3 9.3" stroke="#a48b45" stroke-width="1.6"/></svg>Suchen</li>
      </ul>
      <div class="social"><span></span><span></span><span></span><span></span></div>
    </aside>
    <main class="main">
      <div class="photo" role="img" aria-label="Hintergrundfoto: Stahl-Glas-Gitterkonstruktion einer Dachkuppel in dunklem Blaugrau"></div>
      <div class="topbar">
        <span class="item"><svg viewBox="0 0 10 10"><path d="M2 0.5 3.6 2.6 2.7 3.8C3.4 5.3 4.7 6.6 6.2 7.3L7.4 6.4 9.5 8 8.6 9.5C4.5 9.3.7 5.5.5 1.4Z"/></svg>+49 (0)211 - 555 012 40</span>
        <span class="item"><svg viewBox="0 0 10 10"><circle cx="5" cy="5" r="4.2" fill="none" stroke="#a48b45" stroke-width="1.1"/><path d="M5 2.5V5H7" fill="none" stroke="#a48b45" stroke-width="1.1"/></svg>Mo - Fr 9.00 - 18.00</span>
        <span class="item"><svg viewBox="0 0 10 10"><path d="M0 2h10v6H0z"/><path d="M0 2 5 5.5 10 2" fill="none" stroke="#03253f" stroke-width=".8"/></svg>info@brandtner-immo.de</span>
        <span class="item"><svg viewBox="0 0 10 10"><path d="M5 0C3 0 1.6 1.5 1.6 3.4 1.6 6 5 10 5 10S8.4 6 8.4 3.4C8.4 1.5 7 0 5 0Zm0 4.8A1.4 1.4 0 1 1 5 2a1.4 1.4 0 0 1 0 2.8Z"/></svg>Lindenallee 12, 40210 Düsseldorf</span>
      </div>
      <div class="kicker">PROJEKTMANAGEMENT &amp; PROJEKTSTEUERUNG</div>
      <h1 class="headline">WIR REALISIEREN<br>BAUVORHABEN</h1>
      <div class="cards">
        <article class="card">
          <div class="cat">Betriebswirtschaftliche Planung</div>
          <h3>Stet clita kasd gubergren no sea takimata sanctus est lorem</h3>
          <p>Lorem ipsum dolor sit amet, consetetur sadipscing elitr, sed diam nonumy eirmod tempor invidunt ut labore et dolore magna aliquyam erat, sed diam voluptua.</p>
          <span class="more">WEITERLESEN</span>
        </article>
        <article class="card">
          <div class="cat">Steuerung der baulichen Umsetzung</div>
          <h3>Stet clita kasd gubergren no sea takimata sanctus est lorem</h3>
          <p>Lorem ipsum dolor sit amet, consetetur sadipscing elitr, sed diam nonumy eirmod tempor invidunt ut labore et dolore magna aliquyam erat, sed diam voluptua.</p>
          <span class="more">WEITERLESEN</span>
        </article>
        <article class="card">
          <div class="cat">Marketing und Vertrieb</div>
          <h3>Stet clita kasd gubergren no sea takimata sanctus est lorem</h3>
          <p>Lorem ipsum dolor sit amet, consetetur sadipscing elitr, sed diam nonumy eirmod tempor invidunt ut labore et dolore magna aliquyam erat, sed diam voluptua.</p>
          <span class="more">WEITERLESEN</span>
        </article>
      </div>
      <footer class="footer">© 2017 Brandtner Real Estate GmbH - Impressum</footer>
    </main>
  </div>
</body>
</html>
```